Business card for Luxury Portable Restroom Trailer company

We are a Luxury Portable Restroom Trailer Company Called FALCRIDGE HIRES. Based in Orange County California. We provide portable restroom trailers for events, such as, Weddings, Concerts, Charity events, Sporting events, Tournaments, Corporate events, ect. We rent and Sell the Luxury restrooms. Our colors are white, grey, and Orange. As you will see in the logo we uploaded.
There are 2 people in the company so the names and titles will change for the 3 people but card will remain the same. Here is the information for each Person: Dwight Penner CFO 555 318-0476
next Person: Leon Marchetti VP 555 318-0476
Next Person: Owen Marchetti CEO 555 318-0476
Information to include on the card: Luxury Restroom Trailers Rental and Sales. Weddings, Concerts, Charity, Sporting and Corp. Events.

```html
<!DOCTYPE html>
<html lang="en">
<head>
<meta charset="utf-8">
<title>Falcridge Hires – Business Card</title>
<link rel="stylesheet" href="https://fonts.googleapis.com/css2?family=Montserrat:wght@400;500;800&display=swap">
<style>
  :root {
    --orange: #e8652a;
    --orange-deep: #e15a22;
    --white: #ffffff;
    --grey-text: #5a5a5a;
    --backdrop-top: #d2d2d2;
    --backdrop-bottom: #a9a9a9;
  }
  * { box-sizing: border-box; margin: 0; padding: 0; }
  html, body { width: 1200px; height: 802px; overflow: hidden; }
  body {
    background: linear-gradient(180deg, var(--backdrop-top), var(--backdrop-bottom));
    font-family: "Montserrat", sans-serif;
    display: flex;
    align-items: center;
    justify-content: center;
    gap: 40px;
  }
  .card {
    position: relative;
    width: 540px;
    height: 309px;
    border-radius: 18px;
    box-shadow: 0 14px 30px rgba(0,0,0,0.28);
    overflow: hidden;
  }
  .card-front { background: var(--white); }
  .card-back {
    background: radial-gradient(circle at 60% 40%, var(--orange), var(--orange-deep));
    display: flex;
    flex-direction: column;
    align-items: center;
    justify-content: center;
  }
  .accent-bar {
    position: absolute;
    left: 0; top: 112px;
    width: 14px; height: 36px;
    background: var(--orange);
  }
  .holder { position: absolute; left: 42px; top: 108px; }
  .holder-name {
    color: var(--orange);
    font-weight: 800;
    font-size: 22px;
    letter-spacing: 0.5px;
    text-transform: uppercase;
  }
  .holder-title { color: var(--grey-text); font-size: 13px; margin-top: 2px; }
  .contact-list { position: absolute; left: 42px; top: 182px; list-style: none; }
  .contact-list li {
    display: flex; align-items: center; gap: 7px;
    color: var(--grey-text); font-size: 12px; line-height: 20px;
  }
  .contact-list svg { width: 10px; height: 10px; fill: var(--orange); }
  .services { position: absolute; left: 42px; top: 250px; font-size: 12px; line-height: 19px; }
  .services-headline { color: var(--orange); font-weight: 500; }
  .services-events { color: var(--grey-text); }
  .brand-seal {
    position: absolute; right: 36px; top: 26px;
    width: 170px; height: 170px;
    border: 9px solid var(--orange);
    border-radius: 50%;
    display: flex; align-items: center; justify-content: center;
    text-align: center;
  }
  .brand-seal-name {
    color: var(--orange); font-weight: 800; font-size: 20px; line-height: 24px;
  }
  .back-name {
    color: var(--white); font-weight: 800; text-align: center;
    font-size: 50px; line-height: 54px; letter-spacing: 1px;
  }
  .back-name span { display: block; font-size: 30px; letter-spacing: 6px; }
</style>
</head>
<body>
  <section class="card card-front">
    <div class="accent-bar"></div>
    <div class="holder">
      <h1 class="holder-name">Owen Marchetti</h1>
      <p class="holder-title">CEO</p>
    </div>
    <ul class="contact-list">
      <li><svg viewBox="0 0 10 10"><path d="M2 0.5l1.8 2-1 1.1a6 6 0 0 0 3.6 3.6l1.1-1 2 1.8-1.2 1.5C4.5 9.5 0.5 5.5 0.5 1.7z"/></svg>555 318-0476</li>
      <li><svg viewBox="0 0 10 10"><path d="M0.5 2h9v6h-9z M0.5 2l4.5 3.5L9.5 2" stroke="#fff" stroke-width="0.8"/></svg>owen@falcridgehires.com</li>
      <li><svg viewBox="0 0 10 10"><circle cx="5" cy="5" r="4.5"/><path d="M0.5 5h9M5 0.5c-2 2.5-2 6.5 0 9M5 0.5c2 2.5 2 6.5 0 9" stroke="#fff" stroke-width="0.7" fill="none"/></svg>www.falcridgehires.com</li>
    </ul>
    <div class="services">
      <p class="services-headline">Luxury Restroom Trailers Rental and Sales</p>
      <p class="services-events">Weddings | Concerts | Charity | Sporting | Corp</p>
    </div>
    <div class="brand-seal">
      <p class="brand-seal-name">FALCRIDGE<br>HIRES</p>
    </div>
  </section>

  <section class="card card-back">
    <p class="back-name">FALCRIDGE<span>HIRES</span></p>
  </section>
</body>
</html>
```